Wordpress theme website for professionals working together

My partner and I are offering business services, my wife in the energy business as mainly as member of the board of commissioners. I am working as interim manager/consultant in the accounting and finance area. Both activities are connected in one company VELMOT BV (dutch ltd). We need a CV based website. Beside this we do some financial and accounting services.

Target Market(s)

small medium business

Font styles to use
Sans Serif

Colors

Designer to choose colors to be used in the design.

Requirements
Must have
• Pictures of both members.
• CLEAN AND SIMPLE
• I LIKE BLACK & WHITE
Nice to have
• I like design like this theme: http://theme.pruxelo-example.com/resume/

```html
<!DOCTYPE html>
<html lang="en">
<head>
<meta charset="utf-8">
<title>Velmot BV – Resume</title>
<link rel="stylesheet" href="https://fonts.googleapis.com/css2?family=Lato:wght@400;700;900&display=swap">
<style>
:root{
  --ink:#1c1c1c;
  --dark:#232323;
  --text:#3a3a3a;
  --muted:#6a6a6a;
  --light:#f1f1f1;
  --hero-bg:#d3d5da;
  --track:#e6e6e6;
  --brand:#1d3563;
  --white:#ffffff;
  --line:#c9c9c9;
}
*{box-sizing:border-box;margin:0;padding:0}
html,body{width:1200px;height:3114px;overflow:hidden}
body{font-family:'Lato',sans-serif;color:var(--text);background:var(--white);position:relative}
section,header,footer{position:relative;width:1200px}
.abs{position:absolute}
h2.section-title{position:absolute;left:0;width:100%;text-align:center;font-weight:900;font-size:33px;color:var(--ink);letter-spacing:.5px}
.body-copy{font-size:14.5px;line-height:23px;color:var(--text)}

/* header */
.site-header{height:104px;background:var(--white)}
.brand{left:74px;top:36px;display:flex;align-items:center;gap:10px}
.brand-mark{width:14px;height:14px;background:#b5121b}
.brand-name{font-size:36px;font-weight:900;color:var(--brand);letter-spacing:-.5px}
.main-nav{right:72px;top:55px;display:flex;gap:32px;font-size:13.5px;color:var(--ink)}
.main-nav .active{font-weight:700}

/* hero */
.hero{height:494px;background:var(--hero-bg);overflow:hidden}
.hero-photo{left:560px;top:0;width:640px;height:494px;background:linear-gradient(100deg,#d3d5da 0%,#b9bcc1 25%,#a08f85 55%,#6f6058 80%,#3a3a44 100%)}
.hero-name{left:82px;top:100px;font-size:48px;line-height:60px;font-weight:400;color:var(--ink)}
.hero-sub{left:85px;top:172px;font-size:20px;color:var(--ink)}
.hero-about{left:85px;top:207px;width:450px;font-size:14.5px;line-height:22.5px;color:#4a4a4a}
.partner-avatar{left:74px;top:356px;width:96px;height:96px;border-radius:50%;background:radial-gradient(circle at 50% 45%,#c29b86,#6d5147 70%,#3b3b44)}
.partner-name{left:197px;top:370px;font-size:20px;font-weight:700;color:var(--ink)}
.partner-btn{left:197px;top:405px;width:117px;height:42px;background:var(--white);font-size:14.5px;color:var(--ink);display:flex;align-items:center;justify-content:center}

/* skills */
.skills{height:477px}
.skills h2{top:28px}
.skill-row{position:absolute;left:0;width:1200px;height:20px}
.skill-label{position:absolute;right:706px;font-size:14.5px;color:var(--ink);top:0}
.skill-track{position:absolute;left:525px;top:4px;width:359px;height:14px;background:var(--track)}
.skill-fill{height:100%;background:var(--dark)}
.skill-value{position:absolute;left:905px;top:0;font-size:14.5px;color:var(--ink)}

/* jobs */
.jobs{height:532px;display:flex}
.jobs-col{width:600px;height:532px;position:relative}
.jobs-current{background:var(--dark);color:var(--white)}
.jobs-past{background:var(--light)}
.jobs-col h2{position:absolute;top:56px;font-size:33px;font-weight:900}
.jobs-current h2{left:137px;color:var(--white)}
.jobs-past h2{left:79px;color:var(--ink)}
.job{position:absolute;width:305px}
.job h3{font-size:20px;font-weight:700;margin-bottom:8px}
.jobs-current .job{left:139px}
.jobs-current .job p{color:var(--white)}
.jobs-past .job{left:77px}
.jobs-past .job h3{color:var(--ink)}

/* education */
.education{height:234px}
.education h2{top:26px}
.edu-item{position:absolute;top:98px;width:300px;text-align:center}
.edu-item h3{font-size:20px;font-weight:400;color:var(--ink);margin-bottom:10px}

/* worked for */
.clients{height:276px;background:var(--light)}
.clients h2{top:38px}
.client-square{left:452px;top:104px;width:75px;height:133px;background:#1e2a3e;display:flex;align-items:center;justify-content:center;font-size:13px;color:var(--white);font-weight:700}
.client-wide{left:560px;top:135px;width:183px;height:75px;background:#1b2f78;display:flex;align-items:center;justify-content:center;font-size:22px;font-weight:700;color:var(--white)}

/* other */
.other{height:405px}
.other h2{top:46px}
.hobby-photo{left:253px;top:121px;width:335px;height:207px;background:linear-gradient(90deg,#3b3026 0%,#8a6a3e 35%,#e8c27a 60%,#9b7a4c 80%,#4a3a2a 100%)}
.hobby-title{left:614px;top:136px;font-size:20px;font-weight:700;color:var(--ink)}
.hobby-text{left:614px;top:170px;width:335px}

/* contact */
.contact{height:401px;background:var(--light)}
.contact h2{top:36px}
.field{position:absolute;background:var(--white);border:1px solid var(--line);font-size:13px;font-weight:700;color:var(--ink);padding:11px 12px}
.field-name{left:253px;top:114px;width:335px;height:40px}
.field-email{left:614px;top:114px;width:333px;height:40px}
.field-message{left:253px;top:164px;width:694px;height:121px}
.submit{left:496px;top:303px;width:208px;height:50px;background:var(--dark);color:var(--white);font-size:18px;font-weight:700;display:flex;align-items:center;justify-content:center}

/* footer */
.site-footer{height:191px}
.footer-nav{left:0;width:100%;top:48px;display:flex;justify-content:center;gap:34px;font-size:13.5px;color:var(--ink)}
.copyright{left:0;width:100%;top:86px;text-align:center;font-size:12.5px;color:var(--muted)}
.social{left:0;width:100%;top:120px;display:flex;justify-content:center;gap:20px}
.social span{width:20px;height:20px;border-radius:50%;background:#4a4a4a}
</style>
</head>
<body>

<header class="site-header">
  <div class="brand abs"><span class="brand-mark"></span><span class="brand-name">Velmot</span></div>
  <nav class="main-nav abs">
    <span class="active">HOME</span><span>ACTUAL JOBS</span><span>FINISHED JOBS</span><span>SKILLS</span><span>EDUCATION</span><span>CONTACT</span><span>MORE...</span>
  </nav>
</header>

<section class="hero">
  <div class="hero-photo abs" role="img" aria-label="Portrait photo of Hendrik, smiling, wearing glasses"></div>
  <h1 class="hero-name abs">Hendrik</h1>
  <div class="hero-sub abs">About me</div>
  <p class="hero-about abs">Nullam condimentum faucibus consequat. Aenean quis leo felis. Morbi hendrerit auctor purus, sed malesuada tortor. Lorem ipsum dolor sit amet, consectetur adipiscing elit. Donec ullamcorper, leo eu sollicitudin malesuada, nibh nunc condimentum lectus..</p>
  <div class="partner-avatar abs" role="img" aria-label="Round portrait photo of partner Marijke"></div>
  <div class="partner-name abs">Marijke</div>
  <div class="partner-btn abs">Click Here</div>
</section>

<section class="skills">
  <h2 class="section-title">SKILLS</h2>
  <div class="skill-row" style="top:119px"><span class="skill-label">Annual reporting</span><div class="skill-track"><div class="skill-fill" style="width:61%"></div></div><span class="skill-value">65%</span></div>
  <div class="skill-row" style="top:160px"><span class="skill-label">Financial monthly reporting</span><div class="skill-track"><div class="skill-fill" style="width:42%"></div></div><span class="skill-value">40%</span></div>
  <div class="skill-row" style="top:202px"><span class="skill-label">Accounting</span><div class="skill-track"><div class="skill-fill" style="width:96%"></div></div><span class="skill-value">98%</span></div>
  <div class="skill-row" style="top:243px"><span class="skill-label">Financial management</span><div class="skill-track"><div class="skill-fill" style="width:76%"></div></div><span class="skill-value">88%</span></div>
  <div class="skill-row" style="top:285px"><span class="skill-label">Project management</span><div class="skill-track"><div class="skill-fill" style="width:71%"></div></div><span class="skill-value">70%</span></div>
  <div class="skill-row" style="top:326px"><span class="skill-label">Team player</span><div class="skill-track"><div class="skill-fill" style="width:100%"></div></div><span class="skill-value">100%</span></div>
  <div class="skill-row" style="top:368px"><span class="skill-label">Trouble shooter</span><div class="skill-track"><div class="skill-fill" style="width:79%"></div></div><span class="skill-value">89%</span></div>
  <div class="skill-row" style="top:409px"><span class="skill-label">ETC.</span><div class="skill-track"><div class="skill-fill" style="width:22%"></div></div><span class="skill-value">15%</span></div>
</section>

<section class="jobs">
  <div class="jobs-col jobs-current">
    <h2>ACTUAL JOBS</h2>
    <div class="job" style="top:120px"><h3>Advisor Kestrel Group</h3><p class="body-copy">Nullam condimentum faucibus consequat. Aenean quis leo felis. Morbi hendrerit auctor purus, sed malesuada tortor...</p></div>
    <div class="job" style="top:250px"><h3>Advisor Lindvaart &amp; Co</h3><p class="body-copy">Nullam condimentum faucibus consequat. Aenean quis leo felis. Morbi hendrerit auctor purus, sed malesuada tortor...</p></div>
  </div>
  <div class="jobs-col jobs-past">
    <h2>FINISHED JOBS</h2>
    <div class="job" style="top:120px"><h3>Controller a.i. Kestrel Group</h3><p class="body-copy">Nullam condimentum faucibus consequat. Aenean quis leo felis. Morbi hendrerit auctor purus, sed malesuada tortor...</p></div>
    <div class="job" style="top:246px"><h3>Advisor Delta Fern</h3><p class="body-copy">Nullam condimentum faucibus consequat. Aenean quis leo felis. Morbi hendrerit auctor purus, sed malesuada tortor...</p></div>
    <div class="job" style="top:374px"><h3>Financial director Norvik</h3><p class="body-copy">Nullam condimentum faucibus consequat. Aenean quis leo felis. Morbi hendrerit auctor purus, sed malesuada tortor...</p></div>
  </div>
</section>

<section class="education">
  <h2 class="section-title">EDUCATION</h2>
  <div class="edu-item" style="left:271px"><h3>Stelvio Institute (RA)</h3><p class="body-copy">Nullam condimentum faucibus consequat. Aenean quis leo felis. Morbi hendrerit auctor purus, sed malesuada tortor...</p></div>
  <div class="edu-item" style="left:630px"><h3>Atheneum B</h3><p class="body-copy">Nullam condimentum faucibus consequat. Aenean quis leo felis. Morbi hendrerit auctor purus, sed malesuada tortor...</p></div>
</section>

<section class="clients">
  <h2 class="section-title">WORKED FOR</h2>
  <div class="client-square abs">Trevan</div>
  <div class="client-wide abs">Korsmit</div>
</section>

<section class="other">
  <h2 class="section-title">OTHER</h2>
  <div class="hobby-photo abs" role="img" aria-label="Photo of a person holding a camera in warm forest light"></div>
  <h3 class="hobby-title abs">Fotography</h3>
  <p class="hobby-text body-copy abs">Nullam condimentum faucibus consequat. Aenean quis leo felis. Morbi hendrerit auctor purus, sed malesuada tortor. Lorem ipsum dolor sit amet, consectetur adipiscing elit. Donec ullamcorper, leo eu sollicitudin malesuada, nibh nunc condimentum lectus..</p>
</section>

<section class="contact">
  <h2 class="section-title">CONTACT US</h2>
  <div class="field field-name">Name</div>
  <div class="field field-email">Email Address</div>
  <div class="field field-message">Message</div>
  <div class="submit abs">SUBMIT</div>
</section>

<footer class="site-footer">
  <nav class="footer-nav abs"><span>HOME</span><span>ACTUAL JOBS</span><span>FINISHED JOBS</span><span>SKILLS</span><span>EDUCATION</span><span>CONTACT</span><span>MORE...</span></nav>
  <p class="copyright abs">Copyright© 2018 Company Name. All Right Reserved</p>
  <div class="social abs"><span></span><span></span><span></span><span></span><span></span></div>
</footer>

</body>
</html>
```